Business Card Design - Amberfield Court

We are looking at a new design for our business cards that has a modern and professional look. We run a residential aged care facility focussing on the care of residents. The cards will be used for potential clients, consultants and business opportunities in this sector. Blue and white is our main colours and would to see these colours incorporated in the design.
Industry/Entity Type
Business
Contact Information for Business Card
Amberfield Court, Darren Walsh, dwalsh@amberfieldcourt.com.au, Finance Manager, 0472 639 208, BCom, 37 Marrabel Crescent, Brindle Vale, Qld 4093.
Look and feel
Each slider illustrates characteristics of the customer's brand and the style your logo design should communicate.

```html
<!DOCTYPE html>
<html lang="en">
<head>
<meta charset="utf-8">
<title>Amberfield Court – Business Card</title>
<link href="https://fonts.googleapis.com/css2?family=Open+Sans:wght@300;400;700&display=swap" rel="stylesheet">
<style>
  :root {
    --stage: #e7e5e2;
    --card-white: #ffffff;
    --brand-blue: #4b7b95;
    --brand-blue-dark: #3f6b84;
    --taupe: #aaa29b;
    --muted-grey: #9a9a9a;
    --on-blue: #ffffff;
  }
  * { box-sizing: border-box; margin: 0; padding: 0; }
  html, body {
    width: 1200px; height: 950px; overflow: hidden;
    background: var(--stage);
    font-family: "Open Sans", Arial, sans-serif;
  }
  .business-card {
    position: absolute; left: 100px; top: 197px;
    width: 1000px; height: 556px;
    background: var(--card-white);
    overflow: hidden;
    box-shadow: 0 12px 30px rgba(0,0,0,.18);
  }
  .wave-background { position: absolute; inset: 0; width: 100%; height: 100%; }
  .brand-lockup {
    position: absolute; left: 90px; top: 120px;
    display: flex; align-items: center; gap: 18px;
  }
  .brand-dot {
    width: 34px; height: 34px; border-radius: 50%;
    background: var(--brand-blue);
  }
  .brand-name {
    font-weight: 700; font-size: 36px; letter-spacing: 2px;
    color: var(--brand-blue); text-transform: uppercase;
  }
  .holder {
    position: absolute; right: 60px; top: 130px; text-align: right;
  }
  .holder-name {
    font-weight: 700; font-size: 34px; color: var(--brand-blue);
    letter-spacing: 1px; text-transform: uppercase;
  }
  .holder-name .credential { font-size: 30px; }
  .holder-role {
    font-weight: 300; font-size: 26px; color: var(--muted-grey);
    letter-spacing: 1.5px; text-transform: uppercase; margin-top: 2px;
  }
  .contact-list {
    position: absolute; right: 60px; top: 370px;
    list-style: none; text-align: right;
    color: var(--on-blue); font-size: 24px; line-height: 38px;
  }
  .contact-item { display: flex; justify-content: flex-end; align-items: center; gap: 14px; }
  .contact-icon { width: 24px; height: 24px; flex: none; }
  .contact-item.address { padding-right: 38px; }
</style>
</head>
<body>
  <article class="business-card">
    <svg class="wave-background" viewBox="0 0 1000 556" preserveAspectRatio="none" aria-hidden="true">
      <path d="M0,300 C250,230 500,330 700,270 C830,230 920,215 1000,220 L1000,246 C900,242 800,258 650,318 C420,405 250,290 0,326 Z" fill="var(--taupe)"/>
      <path d="M0,345 C250,300 420,425 650,335 C800,275 900,255 1000,260 L1000,556 L0,556 Z" fill="var(--brand-blue)"/>
      <path d="M0,372 C230,330 430,455 660,360 C800,300 900,282 1000,286" fill="none" stroke="var(--card-white)" stroke-width="3" opacity=".85"/>
    </svg>

    <div class="brand-lockup">
      <span class="brand-dot"></span>
      <span class="brand-name">Amberfield Court</span>
    </div>

    <div class="holder">
      <h1 class="holder-name">Darren Walsh <span class="credential">BCom</span></h1>
      <p class="holder-role">Finance Manager</p>
    </div>

    <ul class="contact-list">
      <li class="contact-item">0472 639 208
        <svg class="contact-icon" viewBox="0 0 24 24" aria-label="Phone"><path fill="var(--on-blue)" d="M6.6 10.8a15 15 0 0 0 6.6 6.6l2.2-2.2c.3-.3.7-.4 1-.2 1.1.4 2.3.6 3.6.6.6 0 1 .4 1 1V20c0 .6-.4 1-1 1A17 17 0 0 1 3 4c0-.6.4-1 1-1h3.5c.6 0 1 .4 1 1 0 1.3.2 2.5.6 3.6.1.3 0 .7-.2 1z"/></svg>
      </li>
      <li class="contact-item">dwalsh@amberfieldcourt.com.au
        <svg class="contact-icon" viewBox="0 0 24 24" aria-label="Email"><rect x="2" y="5" width="20" height="14" rx="2" fill="var(--on-blue)"/><path d="M3 6l9 7 9-7" fill="none" stroke="var(--brand-blue)" stroke-width="1.8"/></svg>
      </li>
      <li class="contact-item">www.amberfieldcourt.com.au
        <svg class="contact-icon" viewBox="0 0 24 24" aria-label="Website"><circle cx="12" cy="12" r="10" fill="var(--on-blue)"/><path d="M2 12h20M12 2c3 3 3 17 0 20M12 2c-3 3-3 17 0 20" fill="none" stroke="var(--brand-blue)" stroke-width="1.4"/></svg>
      </li>
      <li class="contact-item address">37 Marrabel Crescent, Brindle Vale, Qld 4093.</li>
    </ul>
  </article>
</body>
</html>
```